Veltrano.co - Polar Expeditions Specialists

We need a modern, visually striking business card for Veltrano.co, a company specialized in selling expedition cruises to the most remote regions on Earth, with a focus on the Arctic and Antarctica. The design should instantly communicate that the cardholder is an expert in polar travel. Use clean, premium aesthetics with cool tones like icy blue and white, possibly incorporating polar imagery (ice, glaciers, penguins, etc.)

Attached the logo

Contact Information for Business Card

Feels high-end and trustworthy.. Visually memorable — encourages people to keep it

Colors
0054AA
0677BA
7BADD7
CADEEF
E8F1F8

Requirements
Must have
• ice, glaciers, penguins, montains
Nice to have
• modern, transparente,

```html
<!DOCTYPE html>
<html lang="en">
<head>
<meta charset="utf-8">
<title>Veltrano.co – Business Card</title>
<link rel="stylesheet" href="https://fonts.googleapis.com/css2?family=Poppins:wght@500;600;700&family=Montserrat:wght@400;500&display=swap">
<style>
  :root {
    --page-bg: #e8f1f8;
    --brand-blue: #3a72b8;
    --back-blue: #3774b8;
    --back-ink: #2c63a6;
    --back-tag: #4f84c2;
    --card-white: #ffffff;
    --text-dark: #1c1c1c;
    --mark-top: #7badd7;
    --mark-bottom: #3a72b8;
  }
  * { margin: 0; padding: 0; box-sizing: border-box; }
  html, body { width: 900px; height: 1200px; overflow: hidden; }
  body { background: var(--page-bg); position: relative; font-family: "Montserrat", sans-serif; }

  .card {
    position: absolute;
    border-radius: 24px;
    overflow: hidden;
    box-shadow: 0 10px 24px rgba(0, 40, 90, 0.18);
  }
  .card-front { left: 80px; top: 130px; width: 742px; height: 442px; background: var(--card-white); }
  .card-back  { left: 78px; top: 638px; width: 744px; height: 440px; background: var(--back-blue); }

  .brand { position: absolute; display: flex; align-items: center; }
  .brand-dot { border-radius: 50%; flex: none; }
  .brand-name { font-family: "Poppins", sans-serif; font-weight: 700; line-height: 1; }
  .brand-tagline { position: absolute; font-family: "Poppins", sans-serif; font-weight: 600; white-space: nowrap; }

  .card-front .brand { left: 36px; top: 64px; }
  .card-front .brand-dot { width: 60px; height: 60px; background: var(--brand-blue); margin-right: 44px; }
  .card-front .brand-name { font-size: 44px; color: var(--brand-blue); }
  .card-front .brand-tagline { left: 140px; top: 114px; font-size: 14px; color: var(--brand-blue); }

  .holder-name { position: absolute; left: 35px; top: 190px; font-family: "Poppins", sans-serif; font-weight: 600; font-size: 27px; color: var(--brand-blue); }
  .holder-title { position: absolute; left: 35px; top: 226px; font-size: 16.5px; color: var(--text-dark); }
  .address { position: absolute; left: 35px; top: 270px; font-size: 16.5px; line-height: 20px; color: var(--text-dark); }

  .contacts { position: absolute; left: 35px; top: 331px; list-style: none; }
  .contacts li { display: flex; align-items: center; height: 27.5px; font-size: 16.5px; color: var(--text-dark); }
  .contacts svg { width: 16px; height: 16px; margin-right: 8px; fill: var(--brand-blue); }

  .hero-mark {
    position: absolute; left: 374px; top: 140px; width: 308px; height: 266px;
    border-radius: 140px 140px 8px 8px;
    background: linear-gradient(180deg, var(--mark-top), var(--mark-bottom));
    opacity: 0.9;
  }

  .card-back .brand { left: 170px; top: 196px; }
  .card-back .brand-dot { width: 70px; height: 70px; background: var(--back-ink); margin-right: 22px; }
  .card-back .brand-name { font-size: 56px; color: var(--back-ink); }
  .card-back .brand-tagline { left: 259px; top: 268px; font-size: 19px; color: var(--back-tag); }
</style>
</head>
<body>

<section class="card card-front">
  <div class="brand">
    <span class="brand-dot"></span>
    <span class="brand-name">Veltrano.co</span>
  </div>
  <p class="brand-tagline">Polar Expeditions Specialists</p>

  <h1 class="holder-name">Marcus Ellery</h1>
  <p class="holder-title">Managing Director</p>
  <p class="address">48 Harbor Point Drive<br>Halden, NJ 07412 USA</p>

  <ul class="contacts">
    <li>
      <svg viewBox="0 0 24 24" aria-hidden="true"><path d="M6.6 10.8a15.2 15.2 0 0 0 6.6 6.6l2.2-2.2a1 1 0 0 1 1-.25 11.4 11.4 0 0 0 3.6.57 1 1 0 0 1 1 1V20a1 1 0 0 1-1 1A17 17 0 0 1 3 4a1 1 0 0 1 1-1h3.5a1 1 0 0 1 1 1c0 1.25.2 2.45.57 3.57a1 1 0 0 1-.25 1z"/></svg>
      (555)214-7730
    </li>
    <li>
      <svg viewBox="0 0 24 24" aria-hidden="true"><path d="M2 6h20v12H2z" opacity="0"/><path d="M3 6l9 6 9-6v12H3z"/><path d="M3 5h18l-9 6z"/></svg>
      info@veltrano.co
    </li>
    <li>
      <svg viewBox="0 0 24 24" aria-hidden="true"><path d="M12 2a10 10 0 1 0 0 20 10 10 0 0 0 0-20zm-1 17.9A8 8 0 0 1 4.1 11H7l2 2v1l2 2zm6.9-2.5A2 2 0 0 0 16 16h-1v-3a1 1 0 0 0-1-1H8v-2h2a1 1 0 0 0 1-1V7h2a2 2 0 0 0 2-2v-.4a8 8 0 0 1 2.9 12.8z"/></svg>
      www.veltrano.co
    </li>
  </ul>

  <div class="hero-mark" role="img" aria-label="Large polar bear and penguin silhouette brand mark with small stars"></div>
</section>

<section class="card card-back">
  <div class="brand">
    <span class="brand-dot"></span>
    <span class="brand-name">Veltrano.co</span>
  </div>
  <p class="brand-tagline">Polar Expeditions Specialists</p>
</section>

</body>
</html>
```